RB Halden Electric Yard Sign

Looking to have a yard sign designed that we can place at projects we are working on. Most likely will be 18" H x 24" W but flexible that we can increase the size if necessary. It should include our logo, our phone # 609-555-0147, website rbhaldenelectric.example and slogan, built on integrity, driven by excellence. Colors should match our brand.

```html
<!DOCTYPE html>
<html lang="en">
<head>
<meta charset="UTF-8">
<title>RB Halden Electric Yard Sign</title>
<link href="https://fonts.googleapis.com/css2?family=Montserrat:wght@600;700;800&display=swap" rel="stylesheet">
<style>
  :root {
    --brand-red: #e31e29;
    --brand-navy: #0b3469;
    --sign-white: #ffffff;
    --backdrop: #eceeef;
  }
  * { margin: 0; padding: 0; box-sizing: border-box; }
  html, body {
    width: 1200px;
    height: 1200px;
    overflow: hidden;
    background: var(--backdrop);
    font-family: "Montserrat", Arial, sans-serif;
  }
  .yard-sign {
    position: absolute;
    left: 40px;
    top: 180px;
    width: 1120px;
    height: 840px;
    display: flex;
    flex-direction: column;
    background: var(--sign-white);
    box-shadow: 0 6px 24px rgba(0,0,0,0.12);
  }
  .slogan-band {
    height: 218px;
    background: var(--brand-red);
    border-bottom: 9px solid var(--brand-navy);
    display: flex;
    align-items: center;
    justify-content: center;
    text-align: center;
  }
  .slogan {
    color: var(--sign-white);
    font-weight: 800;
    font-size: 68px;
    line-height: 1.12;
    letter-spacing: 0.5px;
    text-transform: uppercase;
    padding-top: 6px;
  }
  .brand-panel {
    flex: 1;
    display: flex;
    align-items: center;
    justify-content: center;
  }
  .brand-name {
    color: var(--brand-red);
    font-weight: 800;
    font-size: 72px;
    letter-spacing: 2px;
    text-transform: uppercase;
    line-height: 1;
  }
  .contact-band {
    height: 238px;
    background: var(--brand-navy);
    display: flex;
    flex-direction: column;
    align-items: center;
    justify-content: center;
    color: var(--sign-white);
  }
  .phone {
    font-weight: 800;
    font-size: 124px;
    line-height: 1;
    letter-spacing: 1px;
  }
  .web-row {
    margin-top: 22px;
    display: flex;
    align-items: center;
    gap: 18px;
  }
  .web-row .rule {
    width: 200px;
    height: 2px;
    background: var(--sign-white);
  }
  .website {
    font-weight: 600;
    font-size: 40px;
    line-height: 1;
  }
</style>
</head>
<body>
  <main class="yard-sign">
    <header class="slogan-band">
      <h1 class="slogan">Built on integrity,<br>driven by excellence</h1>
    </header>

    <section class="brand-panel">
      <div class="brand-name">RB Halden Electric</div>
    </section>

    <footer class="contact-band">
      <div class="phone">609-555-0147</div>
      <div class="web-row">
        <span class="rule"></span>
        <span class="website">rbhaldenelectric.example</span>
        <span class="rule"></span>
      </div>
    </footer>
  </main>
</body>
</html>
```